Request for Business Card Design

Hi. My name is Marlene, I am looking for a new business card design for my company, Quarrow Signal Instruments, LLC. I really like the design you did for Tarsel Venture and was hoping you could do something similar using our full logo and our mark. I am also open to any raised texture design using our mark. I have attached our full logo, which would need to be somewhere on the card, as well as the mark in both outline and full form, as well as our brand colors / guide. The card does not have to be white, as long as our logo and mark appear. I actually like darker colored business cards more, but am open to all options. If you are interested in working with me, please let me know. We would also take the business card design into letterhead design if you can do that.

```html
<!DOCTYPE html>
<html lang="en">
<head>
<meta charset="utf-8">
<title>Quarrow Signal Instruments – Business Card</title>
<link href="https://fonts.googleapis.com/css2?family=Montserrat:wght@400;500;700;800&display=swap" rel="stylesheet">
<style>
  :root {
    --stage: #1b1b1d;
    --card-dark: #444447;
    --ink: #3a3a3d;
    --blue: #1397c5;
    --paper: #ffffff;
  }
  * { box-sizing: border-box; margin: 0; padding: 0; }
  html, body { width: 1200px; height: 929px; overflow: hidden; }
  body {
    background: var(--stage);
    font-family: "Montserrat", sans-serif;
    position: relative;
  }
  .card {
    position: absolute;
    width: 700px;
    height: 400px;
    left: 250px;
    overflow: hidden;
  }
  .card--front { top: 46px; background: var(--card-dark); }
  .card--back { top: 483px; background: var(--paper); }

  .brand {
    display: flex;
    align-items: center;
    gap: 18px;
  }
  .brand__dot {
    border-radius: 50%;
    background: var(--blue);
    flex: none;
  }
  .brand__name {
    font-weight: 800;
    text-transform: uppercase;
    line-height: 1;
  }
  .brand__name span { display: block; }

  .card--front .brand {
    position: absolute;
    left: 50%; top: 50%;
    transform: translate(-50%, -50%);
  }
  .card--front .brand__dot { width: 78px; height: 78px; }
  .card--front .brand__name { color: #f4f4f4; font-size: 58px; letter-spacing: 4px; }
  .card--front .brand__name span + span { font-size: 17.5px; letter-spacing: 1.6px; margin-top: 6px; }

  .card--back .brand {
    position: absolute;
    right: 40px; top: 38px;
    gap: 12px;
  }
  .card--back .brand__dot { width: 44px; height: 44px; }
  .card--back .brand__name { color: var(--ink); font-size: 32px; letter-spacing: 2.5px; }
  .card--back .brand__name span + span { font-size: 9.8px; letter-spacing: 1px; margin-top: 4px; }

  .person {
    position: absolute;
    left: 48px; top: 168px;
  }
  .person__name {
    font-size: 26px;
    font-weight: 800;
    letter-spacing: 0.5px;
    color: var(--ink);
    text-transform: uppercase;
  }
  .person__name .first { color: var(--blue); }
  .person__role { font-size: 17px; color: #222; margin-top: 2px; }

  .address {
    position: absolute;
    right: 44px; top: 160px;
    text-align: right;
    font-size: 15px;
    line-height: 1.35;
    color: #222;
  }

  .contact {
    position: absolute;
    left: 48px; top: 268px;
    list-style: none;
    font-size: 15px;
    color: #222;
  }
  .contact li { display: flex; align-items: center; gap: 10px; line-height: 24px; }
  .contact svg { width: 16px; height: 16px; fill: var(--blue); flex: none; }

  .wave { position: absolute; left: 0; bottom: 0; width: 700px; height: 400px; pointer-events: none; }
</style>
</head>
<body>

<section class="card card--front" aria-label="Card front">
  <div class="brand">
    <span class="brand__dot"></span>
    <p class="brand__name"><span>Quarrow</span><span>Signal Instruments</span></p>
  </div>
</section>

<section class="card card--back" aria-label="Card back">
  <svg class="wave" viewBox="0 0 700 400" aria-hidden="true">
    <path d="M0 400 L0 384 C160 374 330 354 470 316 C560 290 620 262 700 250 L700 400 Z" fill="var(--card-dark)"/>
    <path d="M0 374 C160 364 330 342 465 304 C560 276 625 246 700 234" fill="none" stroke="var(--blue)" stroke-width="5"/>
  </svg>

  <div class="brand">
    <span class="brand__dot"></span>
    <p class="brand__name"><span>Quarrow</span><span>Signal Instruments</span></p>
  </div>

  <div class="person">
    <h1 class="person__name"><span class="first">Darlo</span> Penwick</h1>
    <p class="person__role">Owner</p>
  </div>

  <p class="address">480 Larkspur Ave, Ste<br>210, Halden, TX 75990</p>

  <ul class="contact">
    <li>
      <svg viewBox="0 0 24 24"><path d="M6.6 10.8a15 15 0 0 0 6.6 6.6l2.2-2.2a1 1 0 0 1 1-.25 11.4 11.4 0 0 0 3.6.57 1 1 0 0 1 1 1V20a1 1 0 0 1-1 1A17 17 0 0 1 3 4a1 1 0 0 1 1-1h3.5a1 1 0 0 1 1 1c0 1.25.2 2.45.57 3.57a1 1 0 0 1-.25 1z"/></svg>
      555.014.2286
    </li>
    <li>
      <svg viewBox="0 0 24 24"><path d="M2 5h20v14H2z M2 5l10 8 10-8" /></svg>
      info@quarrowsignal.com
    </li>
    <li>
      <svg viewBox="0 0 24 24"><circle cx="12" cy="12" r="10"/></svg>
      www.quarrowsignal.com
    </li>
  </ul>
</section>

</body>
</html>
```